Modern web-site for a game changer new health app!

We need a very clean UX / UI design for our company website that will be used to sell our brand to large corporations and their employees. If we find a good match, we'd need you to do the app design and some graphics for ongoing design needs.

For a first of its kind app developed at Brockwell University, making licensed holistic medicine accessible to everyday people through access and curation by democratizing holistic health.

Please read the details attached thoroughly and reach out if you have any questions. Many thanks!
Updates

I've updated our requirements to make it easier, please review new details in the PDF shared. Many thanks!

Final brief refinement just uploaded, much has been simplified with very clear guidelines, please update and apply. thanks much!

Target Market(s)

corporate employees and large C level corporate leaders

Industry/Entity Type

wellness

Number of Pages Required

4 page

Font styles to use
Other font styles liked:
• We need website design now and app and socials after, hoping the designer we choose now can work with us on a regular basis going forward

Requirements
Must have
• clean, modern, minimal rich
Nice to have
• some added touches to give a custom feel
Should not have
• pictures, natural looking images or shapes

```html
<!DOCTYPE html>
<html lang="en">
<head>
<meta charset="utf-8">
<title>AURVA — Health For Everyone</title>
<link href="https://fonts.googleapis.com/css2?family=Roboto:wght@400;500;700&display=swap" rel="stylesheet">
<style>
:root{
  --black:#050505;
  --gold:#f2a20c;
  --amber:#d4860f;
  --rust:#b8380a;
  --orange:#e06c0a;
  --brick:#b8410a;
  --cream:#fcf1d9;
  --cream-soft:#fdf6e6;
  --ink:#1d1d1d;
  --muted:#555;
  --white:#fff;
}
*{box-sizing:border-box;margin:0;padding:0}
html,body{width:1200px;height:5208px;overflow:hidden}
body{position:relative;font-family:'Roboto',sans-serif;color:var(--ink);background:var(--white)}
.abs{position:absolute}
.center{text-align:center;left:0;width:1200px}
.leaf{position:absolute;width:18px;height:22px}

/* hero */
.hero{position:absolute;left:0;top:0;width:1200px;height:640px;background:radial-gradient(ellipse at 80% 60%,#2c3a24 0%,#0b0f08 50%,#000 80%)}
.brand{position:absolute;font-weight:700;color:var(--gold);letter-spacing:2px}
.nav a{position:absolute;top:40px;font-size:15px;color:var(--white);text-decoration:none}
.nav a.active{color:var(--gold)}
.btn{position:absolute;display:flex;align-items:center;justify-content:center;border-radius:24px;background:linear-gradient(180deg,#f2a20c,#d9560a);color:var(--white);font-size:14px;font-weight:500}
.hero-title{position:absolute;top:124px;font-size:68px;font-weight:700;color:var(--gold);text-align:center}
.hero-lead{position:absolute;top:214px;font-size:16px;line-height:26px;color:var(--white);text-align:center}
.feature{position:absolute;top:395px;width:311px;height:290px;background:var(--black);border-radius:22px;color:var(--white);text-align:center}
.feature .ring{position:absolute;left:103px;top:38px;width:106px;height:106px;border-radius:50%;background:var(--cream);border:4px solid var(--gold)}
.feature h3{position:absolute;top:184px;left:0;width:100%;font-size:17px;font-weight:500;line-height:26px}

/* how it works */
.section-title{position:absolute;font-weight:700;color:var(--ink)}
.lead{position:absolute;font-size:16px;line-height:26px;color:var(--muted)}
.step{position:absolute;top:1030px;width:117px;height:117px;border-radius:50%;background:var(--cream)}
.step-label{position:absolute;top:1166px;font-size:19px;font-weight:500;text-align:center;line-height:26px;width:260px}

/* trust */
.trust-bg{position:absolute;left:0;top:1313px;width:1200px;height:960px}
.pill{position:absolute;top:1598px;width:260px;height:378px;border-radius:130px}
.pill .disc{position:absolute;left:37px;top:33px;width:186px;height:186px;border-radius:50%;background:var(--cream)}
.pill span{position:absolute;top:266px;left:0;width:100%;text-align:center;color:var(--white);font-size:24px;font-weight:500}

/* enterprise */
.body-copy{position:absolute;font-size:20px;line-height:33px;color:var(--ink)}
.photo{position:absolute;border-radius:50%}

/* testimonials */
.card{position:absolute;top:3773px;width:477px;height:257px;background:var(--white);border-radius:26px;box-shadow:0 4px 24px rgba(0,0,0,.12)}
.card .avatar{position:absolute;left:28px;top:26px;width:64px;height:64px;border-radius:50%;background:linear-gradient(135deg,#c9b8a6,#7d6a58)}
.card h4{position:absolute;left:110px;top:34px;font-size:20px;font-weight:700}
.card time{position:absolute;left:110px;top:68px;font-size:16px}
.card p{position:absolute;left:42px;top:112px;width:410px;font-size:15px;line-height:29px;color:var(--muted)}

/* contact */
.field{position:absolute;left:113px;width:459px;background:var(--white);border-radius:4px;font-size:11px;color:#555;padding:12px 22px}

/* footer */
.foot-h{position:absolute;top:4888px;font-size:20px;font-weight:500}
.foot-link{position:absolute;font-size:13px;color:#333}
.social{position:absolute;top:5038px;width:30px;height:30px;border-radius:50%;border:1.5px solid #333}
</style>
</head>
<body>

<!-- HERO -->
<header class="hero" role="img" aria-label="Dark photograph of white flowers among green leaves"></header>
<svg class="abs" style="left:0;top:470px" width="1200" height="240" viewBox="0 0 1200 240" aria-hidden="true">
  <path d="M0 110 C300 70 700 260 1200 20 L1200 60 C720 290 300 110 0 160 Z" fill="#fff"/>
  <path d="M0 92 C300 60 700 240 1200 0 L1200 40 C700 270 300 96 0 118 Z" fill="var(--gold)"/>
  <path d="M0 118 C300 96 700 270 1200 40 L1200 70 C700 300 320 130 0 170 Z" fill="#fff"/>
  <path d="M560 210 C800 200 1000 120 1200 50 L1200 85 C1000 160 800 230 560 220 Z" fill="var(--orange)"/>
</svg>
<div class="brand" style="left:113px;top:26px;font-size:56px">AURVA</div>
<nav class="nav">
  <a class="active" style="left:472px">Home</a>
  <a style="left:555px">Complementary</a>
  <a style="left:708px">Enterprise</a>
  <a style="left:820px">Members</a>
</nav>
<div class="btn" style="left:931px;top:26px;width:154px;height:41px">Get Started</div>
<h1 class="hero-title center">Health For Everyone</h1>
<p class="hero-lead center">All-Inclusive Holistic Wellness&nbsp; $25 / month Time tested science<br>changing the lives of millions at a price everyone can afford.</p>
<div class="btn" style="left:523px;top:289px;width:154px;height:40px">Get Started</div>

<div class="feature" style="left:113px"><div class="ring">
  <svg width="98" height="98" viewBox="0 0 98 98" aria-hidden="true"><g fill="none" stroke="#333" stroke-width="2"><circle cx="49" cy="38" r="6"/><path d="M49 46v18M37 64h24M33 54c6 0 12 4 16 10 4-6 10-10 16-10"/></g></svg>
</div><h3>1 on 1 with Holistic Doctors<br>&amp; Unlimited Texting</h3></div>
<div class="feature" style="left:444px"><div class="ring">
  <svg width="98" height="98" viewBox="0 0 98 98" aria-hidden="true"><g fill="none" stroke="#333" stroke-width="2"><rect x="32" y="38" width="20" height="28" rx="3"/><rect x="34" y="32" width="16" height="6"/><rect x="54" y="46" width="14" height="20" rx="3"/></g></svg>
</div><h3>Personalized Custom<br>Supplements</h3></div>
<div class="feature" style="left:776px"><div class="ring">
  <svg width="98" height="98" viewBox="0 0 98 98" aria-hidden="true"><g fill="none" stroke="#333" stroke-width="2"><circle cx="49" cy="49" r="14"/><circle cx="49" cy="28" r="4"/><circle cx="49" cy="70" r="4"/><circle cx="28" cy="49" r="4"/><circle cx="70" cy="49" r="4"/></g></svg>
</div><h3>Gut, Hormone &amp; Cellular<br>Lab Tests</h3></div>

<!-- HOW IT WORKS -->
<svg class="leaf" style="left:591px;top:794px" viewBox="0 0 18 22" aria-hidden="true"><path d="M3 20 C2 10 8 3 16 1 C16 10 11 18 3 20Z" fill="var(--gold)"/></svg>
<h2 class="section-title center" style="top:822px;font-size:40px;text-align:center">How It Works</h2>
<p class="lead center" style="top:896px;text-align:center">Sign-up and get a full read of your unique constitution and what makes it thrive with a custom<br>plan made one on one with your on-demand holistic Doctor/Educator. Unlimited texting to<br>address your plan or any other concern you have about your health.</p>
<svg class="abs" style="left:380px;top:1050px" width="450" height="80" viewBox="0 0 450 80" aria-hidden="true"><g fill="none" stroke="var(--rust)" stroke-width="1.5" stroke-dasharray="4 4"><path d="M0 50 C60 70 120 70 165 55"/><path d="M280 20 C330 0 390 5 445 22"/></g></svg>
<div class="step" style="left:267px"><svg width="117" height="117" viewBox="0 0 117 117" aria-hidden="true"><g fill="none" stroke="#222" stroke-width="3"><circle cx="55" cy="62" r="26"/><circle cx="55" cy="55" r="8"/><path d="M40 78c4-8 26-8 30 0M76 34v14M69 41h14"/></g></svg></div>
<div class="step" style="left:542px"><svg width="117" height="117" viewBox="0 0 117 117" aria-hidden="true"><g fill="none" stroke="#222" stroke-width="3"><rect x="38" y="32" width="36" height="50" rx="3"/><path d="M46 44h20M46 54h20M46 64h14"/></g></svg></div>
<div class="step" style="left:825px"><svg width="117" height="117" viewBox="0 0 117 117" aria-hidden="true"><g fill="none" stroke="#222" stroke-width="3"><rect x="34" y="32" width="36" height="50" rx="3"/><path d="M40 44l3 3 5-6M52 44h12M40 56l3 3 5-6M52 56h12M40 68l3 3 5-6M52 68h12"/><circle cx="76" cy="72" r="9"/></g></svg></div>
<div class="step-label" style="left:195px">Sign Up</div>
<div class="step-label" style="left:470px">Get a full read<br>of your constitution</div>
<div class="step-label" style="left:756px">Get a Custom plan</div>

<!-- TRUST -->
<svg class="trust-bg" viewBox="0 0 1200 960" preserveAspectRatio="none" aria-hidden="true"><path d="M0 0 H1200 V880 C1050 820 950 900 800 880 C650 860 500 920 350 900 C200 880 100 960 0 930 Z" fill="var(--cream)"/></svg>
<svg class="leaf" style="left:591px;top:1394px" viewBox="0 0 18 22" aria-hidden="true"><path d="M3 20 C2 10 8 3 16 1 C16 10 11 18 3 20Z" fill="var(--gold)"/></svg>
<h2 class="section-title center" style="top:1430px;font-size:40px;line-height:56px;text-align:center">Our Clients Trust Us to Provide Holistic Health<br>for Their Team, So Should You!</h2>
<div class="pill" style="left:156px;background:var(--amber)"><div class="disc"><svg width="186" height="186" viewBox="0 0 186 186" aria-hidden="true"><g fill="none" stroke="#444" stroke-width="1.5"><circle cx="93" cy="93" r="66"/><circle cx="93" cy="70" r="24"/><circle cx="93" cy="116" r="24"/><circle cx="70" cy="93" r="24"/><circle cx="116" cy="93" r="24"/></g></svg></div><span>Any Challenge</span></div>
<div class="pill" style="left:473px;background:var(--rust)"><div class="disc"><svg width="186" height="186" viewBox="0 0 186 186" aria-hidden="true"><g fill="none" stroke="#333" stroke-width="2"><circle cx="93" cy="93" r="66" stroke-dasharray="3 3"/><circle cx="93" cy="93" r="52"/><path d="M93 93V58M93 93l20 10"/></g></svg></div><span>Anytime</span></div>
<div class="pill" style="left:790px;background:var(--orange)"><div class="disc"><svg width="186" height="186" viewBox="0 0 186 186" aria-hidden="true"><g fill="none" stroke="#444" stroke-width="2"><circle cx="93" cy="93" r="66"/><circle cx="93" cy="93" r="36"/><ellipse cx="93" cy="93" rx="16" ry="36"/><path d="M57 93h72M62 76h62M62 110h62"/></g></svg></div><span>Anywhere</span></div>
<div class="abs center" style="top:2048px;text-align:center;font-size:24px">Trusted by:</div>
<div class="abs center" style="top:2088px;text-align:center;font-size:50px;font-weight:500">Northfield Outfitters</div>

<!-- ENTERPRISE -->
<svg class="leaf" style="left:113px;top:2400px" viewBox="0 0 18 22" aria-hidden="true"><path d="M3 20 C2 10 8 3 16 1 C16 10 11 18 3 20Z" fill="var(--gold)"/></svg>
<h2 class="section-title" style="left:113px;top:2436px;font-size:42px;font-weight:500">Aurva for Enterprise</h2>
<p class="body-copy" style="left:113px;top:2514px;width:465px">We’re all feeling a strain on our health these days Leaders of industry aren’t accidental, they know employee retention &amp; experience work in their favor.</p>
<p class="body-copy" style="left:113px;top:2680px;width:465px">IIn these tumultuous times, Solace brings much-needed relief and benefits to teams that bring their all in return.</p>
<div class="btn" style="left:113px;top:2808px;width:237px;height:41px">Solace For Enterprise</div>
<div class="photo" style="left:630px;top:2380px;width:472px;height:472px;border:8px solid var(--gold);border-left-color:transparent;border-bottom-color:transparent;transform:rotate(20deg)"></div>
<div class="photo" role="img" aria-label="Photo of a woman in a seated yoga pose with arms raised" style="left:632px;top:2396px;width:460px;height:460px;background:linear-gradient(160deg,#e6e8ea,#c9ccd0)"></div>

<!-- HUMAN CARE -->
<svg class="abs" style="left:0;top:2960px" width="1200" height="535" viewBox="0 0 1200 535" aria-hidden="true"><path d="M0 40 C150 -10 300 60 450 50 C600 40 650 -10 800 30 C950 70 1050 20 1200 40 V535 H0 Z" fill="var(--cream)"/></svg>
<div class="abs" style="left:92px;top:3160px;width:480px;height:318px;background:#1a1a1a;border-radius:14px 14px 0 0"></div>
<div class="abs" role="img" aria-label="Photo of a woman meditating cross-legged on a terrace with plants" style="left:104px;top:3172px;width:456px;height:300px;background:linear-gradient(180deg,#dfe6ea,#a9b59e)"></div>
<div class="abs" style="left:36px;top:3478px;width:590px;height:14px;background:linear-gradient(180deg,#cfcfd3,#8c8c92);border-radius:0 0 10px 10px"></div>
<svg class="leaf" style="left:667px;top:3113px" viewBox="0 0 18 22" aria-hidden="true"><path d="M3 20 C2 10 8 3 16 1 C16 10 11 18 3 20Z" fill="var(--gold)"/></svg>
<h2 class="section-title" style="left:667px;top:3148px;font-size:44px;line-height:60px;font-weight:500">Human Care Powered<br>by Technology</h2>
<div class="abs" style="left:667px;top:3290px;font-size:20px;font-weight:500">All Your Mind Body Needs Met In One Place</div>
<p class="body-copy" style="left:667px;top:3346px;width:420px;font-size:20px">All practitioners work collaboratively to provide the best care.</p>

<!-- TESTIMONIALS -->
<svg class="leaf" style="left:591px;top:3636px" viewBox="0 0 18 22" aria-hidden="true"><path d="M3 20 C2 10 8 3 16 1 C16 10 11 18 3 20Z" fill="var(--gold)"/></svg>
<h2 class="section-title center" style="top:3674px;font-size:40px;font-weight:500;text-align:center">Our Testimonials</h2>
<svg class="abs" style="left:66px;top:3912px" width="22" height="26" viewBox="0 0 22 26" aria-hidden="true"><path d="M16 3L6 13l10 10" fill="none" stroke="var(--gold)" stroke-width="4"/></svg>
<svg class="abs" style="left:1104px;top:3912px" width="22" height="26" viewBox="0 0 22 26" aria-hidden="true"><path d="M6 3l10 10-10 10" fill="none" stroke="var(--gold)" stroke-width="4"/></svg>
<article class="card" style="left:109px"><div class="avatar" role="img" aria-label="Portrait photo of Carrie"></div><h4>CARRIE | FIELD OPERATIONS</h4><time>April 11, 2016</time><p>I had no idea that being healthy would actually be this easy and fun. Workouts and nutrition used to be a source of stress for me. It’s so interesting how proper knowledge and techniques can change everything!</p></article>
<article class="card" style="left:614px"><div class="avatar" role="img" aria-label="Portrait photo of Iris"></div><h4>IRIS | ACCOUNTING</h4><time>June 26, 2016</time><p>I’m so glad that I chose Solace for our company. Who knew that something that I could just expense from petty cash would transform the lives of so many people here including myself.</p></article>

<!-- CONTACT -->
<svg class="abs" style="left:0;top:4145px" width="1200" height="720" viewBox="0 0 1200 720" aria-hidden="true">
  <path d="M0 0 H1200 V560 C900 640 500 620 0 570 Z" fill="var(--brick)"/>
  <path d="M0 570 C400 640 800 650 1200 560 V600 C800 690 400 680 0 610 Z" fill="#fff"/>
  <path d="M0 590 C400 660 800 660 1200 580 V596 C800 680 400 680 0 606 Z" fill="var(--gold)"/>
  <path d="M150 690 C500 700 850 670 1200 600 V618 C850 690 500 712 150 700 Z" fill="var(--orange)"/>
</svg>
<h2 class="abs" style="left:113px;top:4220px;font-size:36px;font-weight:500;color:#fff">WE'D LOVE TO HEAR FROM YOU</h2>
<div class="field" style="top:4296px;height:41px">First Name</div>
<div class="field" style="top:4359px;height:41px">Last Name</div>
<div class="field" style="top:4422px;height:40px">Phone Number</div>
<div class="field" style="top:4482px;height:89px">Message</div>
<div class="abs" style="left:113px;top:4605px;width:459px;height:41px;background:#000;border-radius:22px;color:#fff;font-size:15px;font-weight:700;display:flex;align-items:center;justify-content:center">SUBMIT NOW</div>
<div class="photo" style="left:641px;top:4270px;width:460px;height:460px;background:var(--cream-soft)"></div>
<div class="photo" role="img" aria-label="Photo of a woman meditating outdoors in soft light" style="left:670px;top:4300px;width:402px;height:402px;background:radial-gradient(circle at 50% 40%,#e9e0c8,#8a9a6a)"></div>

<!-- FOOTER -->
<div class="brand" style="left:141px;top:4920px;font-size:68px">AURVA</div>
<div class="social" style="left:174px"></div>
<div class="social" style="left:214px"></div>
<div class="social" style="left:254px"></div>
<div class="social" style="left:294px"></div>
<div class="foot-h" style="left:460px">Quick Links</div>
<div class="foot-link" style="left:463px;top:4938px">Home</div>
<div class="foot-link" style="left:463px;top:4964px">Complementary</div>
<div class="foot-link" style="left:463px;top:4990px">Enterprise</div>
<div class="foot-link" style="left:463px;top:5016px">Members</div>
<div class="foot-h" style="left:630px">About Company</div>
<div class="foot-link" style="left:630px;top:4938px">Terms &amp; Conditions</div>
<div class="foot-link" style="left:630px;top:4964px">Privacy Policy</div>
<div class="foot-link" style="left:630px;top:4990px">Support</div>
<div class="foot-link" style="left:630px;top:5016px">Site Map</div>
<div class="foot-link" style="left:630px;top:5042px">Support</div>
<div class="foot-h" style="left:838px">Contact Us</div>
<svg class="abs" style="left:843px;top:4936px" width="14" height="14" viewBox="0 0 14 14" aria-hidden="true"><path d="M3 1l3 3-2 2c1 2 2 3 4 4l2-2 3 3-2 2C6 13 1 8 1 3z" fill="var(--rust)"/></svg>
<div class="foot-link" style="left:870px;top:4932px;font-size:11px;font-weight:700">Phone</div>
<div class="foot-link" style="left:870px;top:4954px">555-014-2288</div>
<svg class="abs" style="left:843px;top:4986px" width="14" height="12" viewBox="0 0 14 12" aria-hidden="true"><rect x="0" y="1" width="14" height="10" fill="var(--rust)"/><path d="M0 1l7 6 7-6" fill="none" stroke="#fff"/></svg>
<div class="foot-link" style="left:870px;top:4982px;font-size:11px;font-weight:700">Email</div>
<div class="foot-link" style="left:870px;top:5004px">info@aurva.com</div>
<svg class="abs" style="left:845px;top:5034px" width="12" height="16" viewBox="0 0 12 16" aria-hidden="true"><path d="M6 0a6 6 0 0 1 6 6c0 4-6 10-6 10S0 10 0 6a6 6 0 0 1 6-6z" fill="var(--rust)"/><circle cx="6" cy="6" r="2" fill="#fff"/></svg>
<div class="foot-link" style="left:870px;top:5032px;font-size:11px;font-weight:700">Location</div>
<div class="foot-link" style="left:870px;top:5054px;line-height:18px;width:230px">301 Nemo enim ipsam voluptatem quia voluptas&nbsp; 255</div>
<div class="abs" style="left:113px;top:5125px;width:974px;height:1px;background:#ddd"></div>
<div class="abs" style="left:1109px;top:5111px;width:32px;height:32px;border-radius:50%;background:var(--rust)"><svg width="32" height="32" viewBox="0 0 32 32" aria-hidden="true"><path d="M10 19l6-6 6 6" fill="none" stroke="#fff" stroke-width="2.5"/></svg></div>
<div class="abs center" style="top:5152px;text-align:center;font-size:13px;color:#444">2025 Copyright -&nbsp; AURVA | All Rights Reserved</div>

</body>
</html>
```